KVR Inc Web Design

WHAT ARE WE DOING?
We are developing a new website look and feel for a new company called KVR Inc. This new look and feel should include colors, design elements, choice of photography and other imagery, fonts, and other user experience elements.

WHAT DO THEY DO?
KVR, Inc, makes tools for researchers who are studying protein-protein interactions. These molecules are the basic tools of biology, and serve as key targets for drug developers and disease researchers. The world of proteins is enormously complex, and companies like KVR provide researchers with critical tools that help them elucidate this world.

WHO ARE WE TALKING TO?
The target audience for this website are professional scientists working in university research or biopharma drug development. They are highly sophisticated consumers looking for key tools that will advance their research.

WHAT DO WE WANT THEM TO DO?
The site is an information resource for the customer exploring the tools that KVR sells and the scientific issues surrounding protein-protein interactions. They should be able to navigate easily to their content of choice, while the whole site should convey a professionalism that enhanced KVR’s credibility.

WHAT DOES THE KVR BRAND STAND FOR?
KVR stands for illumination. Proteins are challenging to study, and KVR exists to help shed light on their workings.

WHAT ARE THE KEY VALUES OF THE KVR BRAND?
Integrity. Innovation. Insight.

WHAT ARE THE EXECUTIONAL MANDITORIES?
The look and feel is completely up for grabs. Nothing is off the table.

WHAT ARE THE DELIVERABLES?
We need new designs for the following templates:
http://cms.marlowbench.com/
http://cms.marlowbench.com/products-and-services/instruments-3/bench-top-instruments/
http://cms.marlowbench.com/category/lab-study/

```html
<!DOCTYPE html>
<html lang="en">
<head>
<meta charset="utf-8">
<title>KVR Inc — Protein-Protein Interactions</title>
<link href="https://fonts.googleapis.com/css2?family=Montserrat:wght@300;400;600;700&family=Open+Sans:wght@400&display=swap" rel="stylesheet">
<style>
:root{
  --orange:#f7a836;
  --teal:#2a8aa8;
  --ink:#3a3a3a;
  --nav:#555;
  --footer:#3b3939;
  --footer-text:#cfcfcf;
  --white:#fff;
}
*{margin:0;padding:0;box-sizing:border-box}
html,body{width:1200px;height:775px;overflow:hidden;background:var(--white)}
body{font-family:"Open Sans",sans-serif;color:var(--ink)}
.page{position:relative;width:1200px;height:775px;overflow:hidden}

.site-header{position:absolute;top:0;left:0;width:1200px;height:54px;background:var(--white);border-top:3px solid var(--orange);z-index:3;box-shadow:0 1px 3px rgba(0,0,0,.12)}
.site-header .pointer{position:absolute;left:474px;top:0;width:0;height:0;border-left:6px solid transparent;border-right:6px solid transparent;border-top:7px solid var(--orange)}
.brand{position:absolute;left:161px;top:12px;font-family:"Montserrat",sans-serif;font-weight:300;font-size:26px;letter-spacing:5px;color:#555;white-space:nowrap}
.main-nav{position:absolute;left:331px;top:19px;display:flex;gap:16px;font-family:"Montserrat",sans-serif;font-weight:600;font-size:13px;letter-spacing:-.3px;color:var(--nav);white-space:nowrap}
.main-nav .active{color:var(--orange)}
.search{position:absolute;left:913px;top:14px;width:126px;height:22px;background:#8a8a8a;color:#ddd;font-size:12px;padding:3px 7px}
.search svg{position:absolute;right:5px;top:5px}

.hero{position:absolute;top:54px;left:0;width:1200px;height:663px;background:linear-gradient(100deg,#e4e4e2 0%,#d9d8d4 30%,#cfc9c0 55%,#c8c2ba 75%,#e2e0dc 100%)}
.features-bg{position:absolute;top:517px;left:0;width:1200px;height:200px;background:rgba(255,255,255,.82);border-top:1px solid #ddd}

.slide{position:absolute;top:54px;left:0;width:1200px;height:463px}
.slide-icon{position:absolute;left:536px;top:159px}
.slide-title{position:absolute;top:215px;width:1200px;text-align:center;font-family:"Montserrat",sans-serif;font-weight:700;font-size:30px;color:var(--ink);letter-spacing:-.3px}
.slide-caption{position:absolute;left:322px;top:267px;width:556px;height:30px;background:rgba(85,85,85,.85);color:var(--white);font-size:12.5px;line-height:30px;text-align:center}
.slide-next{position:absolute;left:584px;top:322px}
.arrow{position:absolute;top:222px}
.arrow.prev{left:116px}
.arrow.next{left:1060px}

.features{position:absolute;top:517px;left:0;width:1200px;height:200px}
.feature{position:absolute;top:0;width:310px;height:200px;text-align:center}
.feature.highlight{background:radial-gradient(ellipse at center,#fffaf2 0%,#fdebd0 100%);box-shadow:0 0 4px rgba(0,0,0,.15)}
.feature h2{margin-top:34px;font-family:"Montserrat",sans-serif;font-weight:700;font-size:23px;color:var(--ink)}
.feature.highlight h2{color:var(--orange)}
.feature p{margin:6px auto 0;width:285px;font-size:13px;line-height:17px;color:#222}
.btn{display:block;margin:12px auto 0;width:156px;height:26px;line-height:26px;font-family:"Montserrat",sans-serif;font-size:14px;color:var(--white);background:var(--teal)}
.feature.highlight .btn{background:var(--orange)}

.site-footer{position:absolute;top:717px;left:0;width:1200px;height:58px;background:var(--footer)}
.footer-nav{position:absolute;left:160px;top:22px;font-size:12px;color:var(--footer-text)}
.footer-nav span{margin:0 6px}
.social{position:absolute;left:805px;top:19px;display:flex;gap:5px}
.social svg{display:block}
.copyright{position:absolute;left:901px;top:22px;font-size:12.5px;color:var(--footer-text)}
</style>
</head>
<body>
<div class="page">
  <header class="site-header">
    <div class="pointer"></div>
    <div class="brand">KVR INC</div>
    <nav class="main-nav">
      <span>Company</span><span class="active">Products &amp; Services</span><span>Learning Center</span><span>Events</span><span>KVR News</span><span>Contact</span>
    </nav>
    <div class="search">Search
      <svg width="12" height="12" viewBox="0 0 12 12"><circle cx="5" cy="5" r="3.8" fill="none" stroke="#ccc" stroke-width="1.4"/><line x1="8" y1="8" x2="11" y2="11" stroke="#ccc" stroke-width="1.6"/></svg>
    </div>
  </header>

  <div class="hero" role="img" aria-label="Photo of scientists in lab coats examining a flask of blue liquid, with glassware blurred in the background"></div>
  <div class="features-bg"></div>

  <section class="slide">
    <svg class="slide-icon" width="128" height="64" viewBox="0 0 128 64">
      <line x1="0" y1="30" x2="38" y2="30" stroke="#555" stroke-dasharray="3 2"/>
      <line x1="90" y1="30" x2="128" y2="30" stroke="#555" stroke-dasharray="3 2"/>
      <polygon points="64,3 86,16 86,44 64,57 42,44 42,16" fill="rgba(255,255,255,.35)" stroke="#444" stroke-width="1.5"/>
      <path d="M60 17 h8 M61 17 v9 l-8 14 h22 l-8 -14 v-9" fill="none" stroke="#333" stroke-width="1.6"/>
      <path d="M56 35 h16 l3 5 h-22z" fill="#333"/>
    </svg>
    <h1 class="slide-title">Welcome to Protein-Protein Interactions</h1>
    <div class="slide-caption">Lorem ipsum dolor sit amet, consectetur adipiscing elit. Proin placerat nulla massa,</div>
    <svg class="slide-next" width="32" height="32" viewBox="0 0 32 32">
      <circle cx="16" cy="16" r="15" fill="none" stroke="#333" stroke-width="1.5"/>
      <circle cx="16" cy="16" r="11" fill="#333"/>
      <path d="M11 16 h9 M17 12 l4 4 -4 4" fill="none" stroke="#bbb" stroke-width="2"/>
    </svg>
    <svg class="arrow prev" width="26" height="40" viewBox="0 0 26 40"><path d="M20 4 L6 20 L20 36" fill="none" stroke="#444" stroke-width="6"/></svg>
    <svg class="arrow next" width="26" height="40" viewBox="0 0 26 40"><path d="M6 4 L20 20 L6 36" fill="none" stroke="#444" stroke-width="6"/></svg>
  </section>

  <section class="features">
    <div class="feature" style="left:132px">
      <h2>Innovation</h2>
      <p>Lorem ipsum dolor sit amet, consectetur adipiscing elit. Proin placerat nulla massa, condimentum leo tincidunt vel. Consectetur adipiscing elit.</p>
      <span class="btn">Learn More</span>
    </div>
    <div class="feature highlight" style="left:446px">
      <h2>Automation</h2>
      <p>Lorem ipsum dolor sit amet, consectetur adipiscing elit. Proin placerat nulla massa, condimentum leo tincidunt vel. Consectetur adipiscing elit.</p>
      <span class="btn">Order Today</span>
    </div>
    <div class="feature" style="left:757px">
      <h2>Research</h2>
      <p>Lorem ipsum dolor sit amet, consectetur adipiscing elit. Proin placerat nulla massa, condimentum leo tincidunt vel. Consectetur adipiscing elit.</p>
      <span class="btn">The Challenge</span>
    </div>
  </section>

  <footer class="site-footer">
    <div class="footer-nav">Company<span>-</span>Products &amp; Services<span>-</span>Learning Center<span>-</span>Events<span>-</span>KVR News<span>-</span>Contact</div>
    <div class="social" aria-label="Share links">
      <svg width="22" height="22" viewBox="0 0 22 22" aria-label="Email"><circle cx="11" cy="11" r="11" fill="#fff"/><rect x="5.5" y="7.5" width="11" height="7" fill="none" stroke="#3b3939" stroke-width="1.4"/><path d="M5.5 7.5 L11 11.5 L16.5 7.5" fill="none" stroke="#3b3939" stroke-width="1.4"/></svg>
      <svg width="22" height="22" viewBox="0 0 22 22" aria-label="Share"><circle cx="11" cy="11" r="11" fill="#fff"/><circle cx="7" cy="11" r="2" fill="#3b3939"/><circle cx="15" cy="7" r="2" fill="#3b3939"/><circle cx="15" cy="15" r="2" fill="#3b3939"/><path d="M7 11 L15 7 M7 11 L15 15" stroke="#3b3939" stroke-width="1.3"/></svg>
      <svg width="22" height="22" viewBox="0 0 22 22" aria-label="Location"><circle cx="11" cy="11" r="11" fill="#fff"/><path d="M11 17 C8 13 7 11.5 7 9.5 a4 4 0 0 1 8 0 c0 2 -1 3.5 -4 7.5z" fill="#3b3939"/><circle cx="11" cy="9.5" r="1.4" fill="#fff"/></svg>
    </div>
    <div class="copyright">Copyright © KVR Inc. 2013</div>
  </footer>
</div>
</body>
</html>
```